BRISKEL Need a luxury modern business card designed.

Need a luxury modern business card designed. refer to the uploaded files for the company name and logo in the zip file under source files. i will making my descion on monday. so please send in before then so if we need to edit we will have the time. we have a trade show coming up and im on a deadline for printer.

Target Market(s)

high end clients

Contact Information for Business Card

Company nAme and logo. Tobias Fennick Co-Founder / Project Manager Office # 555-318-7094 Cell # 555-642-1586 BRISKEL.CA Tobias@briskel-example.ca

Font styles to use
Other font styles liked:
• Modern

Requirements
Must have
• Company name and logo, contact info, using the black, gold and white color scheme.

```html
<!DOCTYPE html>
<html lang="en">
<head>
<meta charset="utf-8">
<title>Briskel Business Card</title>
<link rel="stylesheet" href="https://fonts.googleapis.com/css2?family=Montserrat:wght@400;500;600&family=Nunito+Sans:wght@400;600&display=swap">
<style>
  :root {
    --stage: #151515;
    --card: #333333;
    --gold: #a8965f;
    --white: #f4f4f2;
    --muted: #d9d9d6;
  }
  * { box-sizing: border-box; margin: 0; padding: 0; }
  html, body { width: 1200px; height: 900px; overflow: hidden; }
  body {
    background: radial-gradient(ellipse at 50% 30%, #2a2a2a 0%, var(--stage) 70%);
    font-family: "Nunito Sans", Arial, sans-serif;
    color: var(--white);
    position: relative;
  }
  .card {
    position: absolute;
    left: 280px;
    width: 640px;
    height: 366px;
    background: var(--card);
    border-left: 4px solid var(--gold);
    border-bottom: 4px solid var(--gold);
    box-shadow: 0 18px 40px rgba(0,0,0,0.55);
  }
  .card--front { top: 56px; }
  .card--back { top: 478px; }

  .wordmark {
    font-family: "Montserrat", Arial, sans-serif;
    font-weight: 400;
    color: var(--white);
    letter-spacing: 0.22em;
    display: flex;
    align-items: center;
    gap: 14px;
  }
  .wordmark__square {
    width: 14px; height: 14px;
    background: var(--gold);
    flex: none;
  }
  .card--front .wordmark {
    position: absolute;
    right: 52px;
    top: 86px;
    font-size: 44px;
  }
  .card--back .wordmark {
    position: absolute;
    right: 44px;
    top: 96px;
    font-size: 34px;
  }

  .holder {
    position: absolute;
    left: 52px;
    top: 52px;
  }
  .holder__name {
    font-family: "Montserrat", Arial, sans-serif;
    font-weight: 600;
    font-size: 22px;
    letter-spacing: 0.04em;
    text-transform: uppercase;
    color: var(--gold);
  }
  .holder__title {
    font-size: 17px;
    color: var(--white);
    margin-top: 2px;
  }
  .divider {
    position: absolute;
    left: 52px;
    right: 44px;
    top: 158px;
    height: 1px;
    background: var(--gold);
  }
  .contact {
    position: absolute;
    left: 52px;
    top: 196px;
    list-style: none;
  }
  .contact__item {
    display: flex;
    align-items: center;
    gap: 12px;
    font-size: 18px;
    line-height: 30px;
    color: var(--white);
  }
  .contact__icon {
    width: 18px; height: 18px;
    flex: none;
    fill: none;
    stroke: var(--gold);
    stroke-width: 1.6;
  }
  .contact__accent { color: var(--gold); }
</style>
</head>
<body>
  <section class="card card--front" aria-label="Card front">
    <div class="wordmark"><span class="wordmark__square"></span>BRISKEL</div>
  </section>

  <section class="card card--back" aria-label="Card back">
    <div class="holder">
      <p class="holder__name">Tobias Fennick</p>
      <p class="holder__title">Co-Founder | Project Manager</p>
    </div>
    <div class="wordmark"><span class="wordmark__square"></span>BRISKEL</div>
    <div class="divider"></div>
    <ul class="contact">
      <li class="contact__item">
        <svg class="contact__icon" viewBox="0 0 20 20"><circle cx="10" cy="10" r="8"/><path d="M7 6.5c0 3.5 3 6.5 6.5 6.5l1-1.5-2-1-1 .8c-1-.5-2-1.5-2.5-2.5l.8-1-1-2z"/></svg>
        555-318-7094
      </li>
      <li class="contact__item">
        <svg class="contact__icon" viewBox="0 0 20 20"><rect x="6" y="2" width="8" height="16" rx="1.5"/><path d="M9 15.5h2"/></svg>
        555-642-1586
      </li>
      <li class="contact__item">
        <svg class="contact__icon" viewBox="0 0 20 20"><rect x="2" y="4.5" width="16" height="11"/><path d="M2 4.5l8 6 8-6"/></svg>
        Tobias@briskel-example.ca
      </li>
      <li class="contact__item">
        <svg class="contact__icon" viewBox="0 0 20 20"><circle cx="10" cy="10" r="8"/><ellipse cx="10" cy="10" rx="3.5" ry="8"/><path d="M2 10h16M3.5 6h13M3.5 14h13"/></svg>
        <span>www.<span class="contact__accent">briskel</span>.ca</span>
      </li>
    </ul>
  </section>
</body>
</html>
```